Website for Dental Office - The Bright Arch Clinic

The bright arch clinic is a dental office offering cosmetic dentistry, general dentistry, and multi-specialty dental care all under one roof in our state-of-the-art cosmetic dental center. We are particularly striving to provide services that fit the need of the young generation. Thus, we hope to have a modern, professional concise website that represents our spirit.

*Should be able to switch from English to Chinese

6 sections besides homepage:
Home, Meet us, Services,
Patient Info, Cases&Reviews, Blog, Contact

The Services sections should contain multiple subsections such as cleaning and prevention, cosmetic dentistry, implant dentistry, removable dentures, etc...
The Patient Info section is also intended to contain several subsections such as
New Patient offer, accepted Insurance, patient portal, helpful tips, etc...

Target Market(s)

young generation

Coding

Coded - Design and coding required

Number of Pages Required

5+ page

Font styles to use
Sans Serif

Colors
0592cd
33a6d7
85cae6
00a990
33b8a4
86cfc6
cee9f5
cfeae6
3277b5

Requirements
Must have
• *Should be able to switch from English to Chinese
Nice to have
• http://www.thebrightarchclinic.com/
• As a reference, the above link is the current website, but we would like to change the appearance and the content (our new logo's picture is attached)

```html
<!DOCTYPE html>
<html lang="en">
<head>
<meta charset="utf-8">
<title>The Bright Arch Clinic</title>
<link href="https://fonts.googleapis.com/css2?family=Hind:wght@500;600&family=Montserrat:wght@400;500;600&display=swap" rel="stylesheet">
<style>
:root{
  --blue:#0592cd; --blue-2:#33a6d7; --blue-3:#85cae6; --blue-pale:#cee9f5;
  --teal:#00a990; --teal-2:#33b8a4; --teal-3:#86cfc6; --teal-pale:#cfeae6;
  --navy:#3277b5; --ink:#333; --muted:#555; --dark:#4a4a4c; --red:#e0251b;
}
*{box-sizing:border-box;margin:0;padding:0}
html,body{width:1200px;height:4089px;overflow:hidden;background:#fff}
body{position:relative;font-family:"Montserrat",sans-serif;color:var(--ink)}
.abs{position:absolute}
h1,h2,h3,.head{font-family:"Hind",sans-serif;font-weight:600}
.shapes{position:absolute;left:0;top:0}

/* header */
.brand{left:111px;top:34px;display:flex;align-items:center;gap:14px}
.brand-mark{width:46px;height:46px;background:var(--blue-2)}
.brand-name{font-family:"Hind",sans-serif;font-weight:600;color:var(--blue-2);font-size:24px;line-height:24px;letter-spacing:.5px}
.lang{left:527px;top:22px;width:137px;height:31px;border:1.5px solid var(--blue);border-radius:16px;display:flex;font-size:12px;overflow:hidden}
.lang span{flex:1;display:flex;align-items:center;justify-content:center}
.lang .on{background:var(--blue);color:#fff;border-radius:16px}
.contact-chip{top:19px;display:flex;gap:12px;align-items:center}
.chip-icon{width:38px;height:38px;border-radius:50%;display:flex;align-items:center;justify-content:center}
.chip-label{font-size:12px;font-weight:600;line-height:19px}
.chip-value{font-size:13px;font-weight:500;color:var(--blue)}
.nav{left:467px;top:83px;display:flex;gap:20px;font-size:16px;color:#222}
.nav .current{color:var(--blue-2)}

/* hero */
.hero-photo{left:600px;top:119px;width:600px;height:516px;background:linear-gradient(135deg,#d9d6d1,#efece8 55%,#c9c3bb)}
.hero-text{left:111px;top:212px;color:#fff;width:480px}
.hero-text h1{font-size:39px;line-height:50px;letter-spacing:.3px;white-space:nowrap}
.hero-text .sub{font-size:21px;font-weight:600;margin-top:18px}
.hero-text p{font-size:13px;line-height:26px;margin-top:18px}
.btn{display:inline-block;border-radius:22px;font-size:13px;padding:12px 17px;line-height:17px}
.btn-white{background:#fff;color:var(--blue-2);margin-top:26px}
.dots{left:111px;top:496px;display:flex;gap:3px}
.dots i{width:14px;height:14px;border-radius:50%;background:rgba(255,255,255,.55)}
.dots i:first-child{background:#fff}

/* headings */
.sec-title{color:var(--blue-2);font-size:34px;letter-spacing:.3px}
.rule{height:2px;background:var(--blue-2)}

/* passion */
.passion{left:111px;top:786px;width:590px}
.passion .rule{width:106px;margin-top:10px}
.passion p{font-size:13px;line-height:22.5px;color:var(--muted);margin-top:26px;text-align:justify}
.btn-blue{background:var(--blue);color:#fff;margin-top:28px}
.ring-photo{border-radius:50%;border:6px solid var(--blue)}
.passion-photo{left:739px;top:754px;width:310px;height:310px;background:linear-gradient(160deg,#e8e1dc,#c7b9ad 60%,#5d7fa8)}
.passion-badge{left:943px;top:948px;width:144px;height:144px;border-radius:50%;background:var(--blue);border:6px solid #fff}

/* services */
.divider{left:330px;top:1175px;width:540px;height:3px;background:var(--blue-2)}
.center{left:0;width:1200px;text-align:center}
.intro{font-size:14px;line-height:21px;color:#333}
.svc-photo{width:302px;height:302px;border-radius:50%}
.svc-card{width:210px;height:210px;border-radius:50%;background:#fff;text-align:center;padding:52px 28px 0;box-shadow:0 2px 6px rgba(0,0,0,.06)}
.svc-card::before{content:"";position:absolute;inset:8px;border-radius:50%;border:1.5px solid var(--teal-3)}
.svc-card h3{color:var(--teal);font-size:17px;line-height:19px;font-weight:500}
.svc-card p{font-size:12px;line-height:18px;color:#555;margin-top:12px}
.svc-card.featured{width:234px;height:234px;background:var(--blue);top:1571px;padding-top:58px}
.svc-card.featured::before{border-color:rgba(255,255,255,.7)}
.svc-card.featured h3,.svc-card.featured p{color:#fff}

/* patient info */
.info-panel{left:111px;top:1889px;width:978px;height:397px;background:#fff;border-top:7px solid var(--blue);border-radius:6px 6px 4px 4px;box-shadow:0 1px 6px rgba(0,0,0,.18)}
.tabs{left:20px;top:45px;display:flex;gap:6px}
.tab{background:var(--teal);color:#fff;font-size:15px;font-weight:500;padding:0 14px;height:35px;line-height:35px;border-radius:4px}
.tab.active{background:var(--blue);position:relative}
.tab.active::after{content:"";position:absolute;left:50%;bottom:-7px;margin-left:-7px;border:7px solid transparent;border-bottom:0;border-top-color:var(--blue)}
.info-text{left:25px;top:119px;width:590px;font-size:13px;line-height:22.5px;color:#444}
.info-text .forms{color:var(--red)}
.info-text .gap{margin-top:14px}
.pay-name{left:22px;top:303px;display:flex;align-items:center;gap:10px;font-size:32px;font-weight:600;color:var(--teal)}
.pay-name i{width:30px;height:30px;background:var(--teal)}
.info-photo{left:651px;top:52px;width:296px;height:296px;border-radius:50%;background:linear-gradient(135deg,#d8c0a8,#efe2d3 50%,#8e6b50)}
.pct{left:840px;top:263px;width:90px;height:90px;border-radius:50%;background:var(--blue);border:5px solid #fff;display:flex;align-items:center;justify-content:center}

/* reviews */
.reviews-title{color:#fff}
.review{width:298px;height:154px;background:#fff;border-radius:3px;padding:18px 13px;box-shadow:0 2px 6px rgba(0,0,0,.2)}
.review p{font-size:12px;line-height:21px;color:#333}
.review p.tight{text-align:justify}
.stars{color:var(--blue);font-size:15px;letter-spacing:1px;margin-top:4px}
.review::after{content:"";position:absolute;left:36px;bottom:-20px;border-left:20px solid #fff;border-bottom:20px solid transparent}
.reviewer{color:#fff;font-size:12px;line-height:20px}
.reviewer b{font-weight:600}
.arrow{width:24px;height:44px}

/* team */
.team-card{top:3182px;width:327px;height:366px;text-align:center}
.team-card.raised{background:#fff;box-shadow:0 1px 6px rgba(0,0,0,.2)}
.avatar{width:150px;height:150px;border-radius:50%;border:5px solid var(--blue);margin:36px auto 0;background:linear-gradient(160deg,#cfc9c2,#6f665d)}
.raised .avatar{border-color:var(--teal)}
.team-card h3{font-family:"Montserrat",sans-serif;font-weight:500;font-size:17px;color:var(--blue);margin-top:30px}
.raised h3{color:var(--teal)}
.team-card .role{font-size:13px;color:#444;text-decoration:underline;margin-top:8px}
.team-card .bio{font-size:12.5px;line-height:22px;color:#444;margin-top:14px;padding:0 10px}

/* contact */
.contact-title{left:111px;top:3756px;color:#fff;font-size:30px;font-family:"Montserrat",sans-serif;font-weight:500}
.c-item{left:111px;display:flex;gap:16px;color:#fff}
.pin{width:40px;height:40px;border-radius:50%;border:2px solid #fff;display:flex;align-items:center;justify-content:center;flex:none;margin-top:6px}
.c-item h4{font-size:20px;font-weight:600}
.c-item p{font-size:15px;line-height:22px}
.foot-name{left:668px;top:3910px;width:421px;text-align:center;color:#fff;font-family:"Hind",sans-serif;font-weight:600;font-size:26px}
.foot-rule{left:668px;top:3999px;width:421px;height:1px;background:#bbb}
.copy{left:668px;top:4031px;width:421px;text-align:center;color:#fff;font-size:13px}
</style>
</head>
<body>

<svg class="shapes" width="1200" height="4089" viewBox="0 0 1200 4089" aria-hidden="true">
  <defs>
    <linearGradient id="heroBlue" x1="0" y1="0" x2="1" y2="1">
      <stop offset="0" stop-color="#3fa4d6"/><stop offset="1" stop-color="#63b9e2"/>
    </linearGradient>
    <linearGradient id="reviewBand" x1="0" y1="0" x2="1" y2="1">
      <stop offset="0" stop-color="#00a990"/><stop offset=".55" stop-color="#2aa7c0"/><stop offset="1" stop-color="#0592cd"/>
    </linearGradient>
  </defs>
  <path d="M0 119H600V717C420 717 200 690 0 635Z" fill="url(#heroBlue)"/>
  <path d="M0 2325Q600 2445 1200 2325V3015Q600 2870 0 3015Z" fill="url(#reviewBand)" role="img" aria-label="Teal backdrop photo of a dentist treating a patient"/>
  <path d="M0 3722Q300 3650 600 3633V4089H0Z" fill="#0592cd"/>
  <path d="M600 3714Q920 3735 1200 3872V4089H600Z" fill="#4a4a4c"/>
</svg>

<!-- header -->
<div class="abs brand"><div class="brand-mark"></div><div class="brand-name">THE BRIGHT ARCH<br>CLINIC</div></div>
<div class="abs lang"><span>English</span><span class="on">Chinese</span></div>
<div class="abs contact-chip" style="left:679px">
  <div class="chip-icon" style="background:var(--blue)"><svg width="16" height="13" viewBox="0 0 16 13"><rect x="1" y="1" width="14" height="11" rx="1.5" fill="none" stroke="#fff" stroke-width="1.8"/><path d="M1.5 2L8 7 14.5 2" fill="none" stroke="#fff" stroke-width="1.8"/></svg></div>
  <div><div class="chip-label">EMAIL:</div><div class="chip-value">info@thebrightarchclinic.com</div></div>
</div>
<div class="abs contact-chip" style="left:935px">
  <div class="chip-icon" style="background:var(--teal)"><svg width="15" height="15" viewBox="0 0 24 24"><path d="M6.6 10.8a15.1 15.1 0 006.6 6.6l2.2-2.2a1 1 0 011-.25 11.4 11.4 0 003.6.57 1 1 0 011 1V20a1 1 0 01-1 1A17 17 0 013 4a1 1 0 011-1h3.5a1 1 0 011 1c0 1.250.2 2.450.57 3.57a1 1 0 01-.25 1z" fill="#fff"/></svg></div>
  <div><div class="chip-label">PHONE:</div><div class="chip-value" style="color:var(--teal)">1-555-014-2280</div></div>
</div>
<nav class="abs nav"><span class="current">HOME</span><span>Meet Us</span><span>Services</span><span>Patient Info</span><span>Cases &amp; Reviews</span><span>Blog</span><span>Contact</span></nav>

<!-- hero -->
<div class="abs hero-photo" role="img" aria-label="Smiling young woman with dark hair"></div>
<div class="abs hero-text">
  <h1>THE BRIGHT ARCH CLINIC</h1>
  <div class="sub">The bright arch clinic is a dental office</div>
  <p>Welcome to The Bright Arch Clinic where we specialize in General and Cosmetic Dentistry, Dental Implants.</p>
  <span class="btn btn-white">Read More</span>
</div>
<div class="abs dots"><i></i><i></i><i></i><i></i><i></i></div>

<!-- passion -->
<section class="abs passion">
  <h2 class="sec-title">“YOUR SMILE. OUR PASSION.”</h2>
  <div class="rule"></div>
  <p>Welcome to The Bright Arch Clinic where we specialize in General and Cosmetic Dentistry, Dental Implants, Periodontics (Gum Surgery), Endodontics (Root Canal Treatment) and Reconstructive Dentistry for patients in Westfield, Lakeview, Millbrook, Ashford, Dunmore, Kelton, Fairhaven, Oakridge and all other surrounding neighborhoods of Westfield, Bayshire.</p>
  <span class="btn btn-blue">Read More</span>
</section>
<div class="abs ring-photo passion-photo" role="img" aria-label="Patient choosing a tooth shade with a dentist"></div>
<div class="abs passion-badge"></div>

<!-- services -->
<div class="abs divider"></div>
<h2 class="abs sec-title center" style="top:1230px">OUR SERVICES</h2>
<p class="abs intro center" style="top:1295px;padding:0 120px">With Eastbrook and Northvale credentials that inspire confidence, we offer cosmetic dentistry, general dentistry and multi-specialty dental care all under one roof in our state-of-the-art cosmetic dental center.</p>
<svg class="abs arrow" style="left:36px;top:1606px" viewBox="0 0 24 44"><path d="M22 2L3 22l19 20" fill="none" stroke="#33a6d7" stroke-width="2"/></svg>
<svg class="abs arrow" style="left:1140px;top:1606px" viewBox="0 0 24 44"><path d="M2 2l19 20L2 42" fill="none" stroke="#33a6d7" stroke-width="2"/></svg>

<div class="abs svc-photo" style="left:112px;top:1389px;background:linear-gradient(160deg,#c98a7a,#e9c9bd 50%,#b66c5e)" role="img" aria-label="Close-up of a bright smile"></div>
<div class="abs svc-photo" style="left:449px;top:1389px;background:linear-gradient(160deg,#f0d8c6,#e9e2dc 55%,#a7d3da)" role="img" aria-label="Tooth shade guide held to a smiling patient"></div>
<div class="abs svc-photo" style="left:784px;top:1389px;background:linear-gradient(160deg,#8e7c70,#d9c7b8 50%,#5a4a40)" role="img" aria-label="Smiling family of four"></div>

<div class="abs svc-card" style="left:158px;top:1583px"><h3>COSMETIC<br>DENTISTRY</h3><p>Veneers are very thin pieces of durable, tooth shaped porcelain that are custom made.</p></div>
<div class="abs svc-card featured" style="left:483px"><h3>IMPLANT<br>DENTISTRY</h3><p>Dental implants are a great way to replace missing teeth and also provide a fixed solution.</p></div>
<div class="abs svc-card" style="left:830px;top:1583px"><h3>MULTI-SPECIALITY<br>TREATMENT</h3><p>Complex oral rehabilitations call for specialized dental care. Our philosophy is founded.</p></div>

<!-- patient info -->
<section class="abs info-panel">
  <div class="abs tabs"><span class="tab active">NEW PATIENT OFFER</span><span class="tab">ACCEPTED INSURANCE</span><span class="tab">PATIENT PORTAL</span><span class="tab">HELPFUL TIPS</span></div>
  <div class="abs info-text">
    <p>Thank you for your trust in us. We look forward to working with you towards a healthy and beautiful smile.</p>
    <p>Prior to your first appointment, we request that you please download and complete:</p>
    <p class="forms">The New Patient Form – Adults or The New Patient Form – Children (16 &amp; Under).</p>
    <p class="gap">We accept most insurance and all major credit cards. We also offer special finance option through SmilePay.</p>
  </div>
  <div class="abs pay-name"><i></i>SmilePay</div>
  <div class="abs info-photo" role="img" aria-label="Two young women smiling together"></div>
  <div class="abs pct"><svg width="44" height="44" viewBox="0 0 44 44"><circle cx="14" cy="14" r="5" fill="none" stroke="#fff" stroke-width="3"/><circle cx="30" cy="30" r="5" fill="none" stroke="#fff" stroke-width="3"/><path d="M32 10L12 34" stroke="#fff" stroke-width="3.5" stroke-linecap="round"/></svg></div>
</section>

<!-- reviews -->
<h2 class="abs sec-title center reviews-title" style="top:2484px">OUR REVIEWS</h2>
<div class="abs" style="left:566px;top:2543px;width:68px;height:2px;background:#fff"></div>
<svg class="abs arrow" style="left:48px;top:2678px" viewBox="0 0 24 44"><path d="M22 2L3 22l19 20" fill="none" stroke="#fff" stroke-width="2"/></svg>
<svg class="abs arrow" style="left:1142px;top:2678px" viewBox="0 0 24 44"><path d="M2 2l19 20L2 42" fill="none" stroke="#fff" stroke-width="2"/></svg>

<div class="abs review" style="left:111px;top:2608px"><p>The Bright Arch Clinic transformed my smile and made me more confident! I was so pleased by the setting and the kindness of the staff.</p><div class="stars">★★★★☆</div></div>
<div class="abs review" style="left:451px;top:2608px"><p class="tight">I LOVE everyone at this office!! Dr. Moreau is the best of the best. The office staff are always courteous and kind, even kept an eye on my granddaughter...</p><div class="stars">★★★★☆</div></div>
<div class="abs review" style="left:791px;top:2608px"><p class="tight">I have been patient of Dr. Varga for quite some time and I wholeheartedly recom mend him! He is dedicated to his patient's wellfare and will do anything...</p><div class="stars">★★★★☆</div></div>

<div class="abs reviewer" style="left:143px;top:2796px"><b>MAYA COLLINS</b><br>10/08/2017</div>
<div class="abs reviewer" style="left:483px;top:2796px"><b>RUTH PALMER</b><br>2/19/2018</div>
<div class="abs reviewer" style="left:823px;top:2796px"><b>LEO K</b><br>5/15/2018</div>

<!-- team -->
<h2 class="abs sec-title center" style="top:3000px">OUR TEAM</h2>
<div class="abs" style="left:566px;top:3057px;width:68px;height:2px;background:var(--blue-2)"></div>
<p class="abs intro center" style="top:3089px;padding:0 130px;font-size:13.5px;color:#444">Welcome to The Bright Arch Clinic where we specialize in General and Cosmetic Dentistry, Dental Implants, Periodontics and Reconstructive Dentistry for patients in Westfield</p>

<div class="abs team-card" style="left:100px">
  <div class="avatar" role="img" aria-label="Portrait of Dr. Lena Moreau"></div>
  <h3>LENA MOREAU, DMD, MS</h3><div class="role">Board Certified Orthodontist</div>
  <p class="bio">Dr. Lena Moreau graduated summa cum laude with a DMD from Eastbrook University School of Dental Medicine.</p>
</div>
<div class="abs team-card raised" style="left:437px">
  <div class="avatar" role="img" aria-label="Portrait of Dr. Peter H. Lindqvist"></div>
  <h3>PETER H. LINDQVIST, DMD</h3><div class="role">Board Certified Orthodontist</div>
  <p class="bio">Dr. Peter Lindqvist is Board Certified by both, the National Board of Youth Dentistry and the National Board of Aligned Orthodontics.</p>
</div>
<div class="abs team-card" style="left:772px">
  <div class="avatar" role="img" aria-label="Portrait of Dr. Nora Salehi"></div>
  <h3>DR. NORA SALEHI, DMD</h3><div class="role">General Dentist</div>
  <p class="bio">Dr. Salehi earned her DMD (Doctor of Dental Medicine) from Eastbrook University School of Dental Medicine .</p>
</div>

<!-- contact -->
<h2 class="abs contact-title">CONTACT US</h2>
<div class="abs c-item" style="top:3818px">
  <div class="pin"><svg width="14" height="18" viewBox="0 0 14 18"><path d="M7 1a6 6 0 00-6 6c0 4.5 6 10 6 10s6-5.5 6-10a6 6 0 00-6-6z" fill="none" stroke="#fff" stroke-width="1.6"/><circle cx="7" cy="7" r="2" fill="#fff"/></svg></div>
  <div><h4>Address:</h4><p>270 Harbor Lane<br>Suite 12, Westfield, MA 02190</p></div>
</div>
<div class="abs c-item" style="top:3912px">
  <div class="pin"><svg width="14" height="18" viewBox="0 0 14 18"><path d="M7 1a6 6 0 00-6 6c0 4.5 6 10 6 10s6-5.5 6-10a6 6 0 00-6-6z" fill="none" stroke="#fff" stroke-width="1.6"/><circle cx="7" cy="7" r="2" fill="#fff"/></svg></div>
  <div><h4>Phone:</h4><p>1-555-014-2280</p></div>
</div>
<div class="abs c-item" style="top:3989px">
  <div class="pin"><svg width="14" height="18" viewBox="0 0 14 18"><path d="M7 1a6 6 0 00-6 6c0 4.5 6 10 6 10s6-5.5 6-10a6 6 0 00-6-6z" fill="none" stroke="#fff" stroke-width="1.6"/><circle cx="7" cy="7" r="2" fill="#fff"/></svg></div>
  <div><h4>Email:</h4><p>info@thebrightarchclinic.com</p></div>
</div>

<div class="abs foot-name">THE BRIGHT ARCH CLINIC</div>
<div class="abs foot-rule"></div>
<div class="abs copy">Copyrights @ 2019 The Bright Arch Clinic. All Rights Reserved.</div>

</body>
</html>
```